Wed site for biomedical device startup

We need a generic website for a medical device startup. I will provide examples below of websites from other companies that can serve as models for what we are looking for. The startup is for a device that can non invasively measure blood flow in the brain using light. The application is to detect the type of stroke someone is having before they get to the hospital so treatment can be started right away. This saves patients upto hours of delayed treatment. Patients will be able to recover from stroke much better and faster as a result. I have attached an AI generated illustration of what the device will ultimately look like for reference.

https://www.372clinicaltech.com
https://vextalune.com

Target Market(s)

Biomedical, medical device, investors of biomedical device startups

Industry/Entity Type

Biomedical

Coding

Coded - Design and coding required

Number of Pages Required

4 page

Requirements
Must have
• same section and section headings as example websites listed above
Nice to have
• similar to example websites listed above. Prefer a darker website over a lighter one. Perhaps dark blues to go with logo colors. A moving background image element at top of landing page could be cool. Something indicative of heartbeat, or neurons, or blood flow.

```html
<!DOCTYPE html>
<html lang="en">
<head>
<meta charset="utf-8">
<title>NEVRA – Biomedical Science</title>
<link rel="stylesheet" href="https://fonts.googleapis.com/css2?family=Poppins:wght@400;500;600;700;800&display=swap">
<style>
  :root {
    --navy: #06053f;
    --navy-deep: #050434;
    --purple: #8e2bd0;
    --violet: #7b3fe4;
    --cyan: #18d2e6;
    --white: #ffffff;
    --ink: #0c0b4a;
    --body-grey: #3d3d4f;
    --accent-gradient: linear-gradient(90deg, #8e2bd0 0%, #18d2e6 100%);
  }
  * { box-sizing: border-box; margin: 0; padding: 0; }
  html, body { width: 1200px; height: 3111px; overflow: hidden; }
  body {
    position: relative;
    background: var(--navy);
    color: var(--white);
    font-family: "Poppins", sans-serif;
  }
  .abs { position: absolute; }

  /* Header */
  .brand { position: absolute; display: flex; align-items: center; gap: 14px; }
  .brand-dot { width: 70px; height: 70px; border-radius: 50%; background: var(--violet); }
  .brand-name { font-weight: 500; font-size: 54px; letter-spacing: 2px; color: var(--white); line-height: 1; }
  .main-nav { position: absolute; top: 48px; left: 460px; display: flex; gap: 33px; font-size: 15px; font-weight: 700; text-transform: uppercase; }
  .main-nav a { color: var(--white); text-decoration: none; }
  .main-nav a.is-active { color: var(--cyan); border-bottom: 1px solid var(--cyan); padding-bottom: 2px; }
  .nav-cta { position: absolute; left: 938px; top: 36px; width: 150px; height: 47px; border: 2px solid var(--white); border-radius: 24px; display: flex; align-items: center; justify-content: center; font-size: 15px; font-weight: 700; }

  /* Hero */
  .hero-title { left: 111px; top: 148px; font-size: 39px; line-height: 48px; font-weight: 800; text-transform: uppercase; width: 460px; }
  .hero-lead { left: 111px; top: 346px; font-size: 22px; line-height: 31px; font-weight: 500; width: 440px; }
  .btn { position: absolute; display: flex; align-items: center; justify-content: center; background: var(--accent-gradient); border-radius: 24px; color: var(--white); font-weight: 700; font-size: 15px; text-transform: uppercase; }

  /* About */
  .about-photo { left: 111px; top: 779px; width: 428px; height: 556px; border-radius: 36px; background: linear-gradient(160deg, #d9d3c6 0%, #a6a39c 45%, #4e4b4f 100%); }
  .about-frame { left: 77px; top: 1200px; width: 171px; height: 169px; border: 2px solid var(--violet); border-radius: 24px; }
  .section-title { font-size: 39px; line-height: 48px; font-weight: 800; text-transform: uppercase; }
  .about-title { left: 599px; top: 798px; width: 500px; }
  .about-copy { left: 599px; top: 968px; width: 492px; font-size: 15.5px; line-height: 24px; font-weight: 500; }
  .about-copy p + p { margin-top: 16px; }

  /* Technologies */
  .tech-heading { left: 0; width: 1200px; top: 1553px; text-align: center; }
  .tech-intro { left: 162px; width: 876px; top: 1622px; text-align: center; font-size: 15.5px; line-height: 24px; font-weight: 600; }
  .tech-card { position: absolute; top: 1725px; width: 304px; height: 362px; background: var(--white); border-radius: 36px 36px 36px 0; text-align: center; color: var(--body-grey); }
  .tech-icon { width: 90px; height: 90px; margin: 38px auto 0; border-radius: 50%; display: flex; align-items: center; justify-content: center; }
  .tech-icon.soft { background: #efe9fb; }
  .tech-icon.solid { background: linear-gradient(135deg, #8e2bd0, #3a6fe0); }
  .tech-card h3 { margin-top: 30px; font-size: 18.5px; font-weight: 700; color: var(--ink); text-transform: uppercase; }
  .tech-card p { margin: 6px auto 0; width: 266px; font-size: 15.5px; line-height: 24px; }

  /* Contact */
  .contact-title { left: 110px; top: 2286px; font-size: 44px; }
  .field-label { position: absolute; font-size: 15px; font-weight: 500; }
  .field { position: absolute; background: var(--white); border-radius: 4px; }
  .contact-photo { left: 643px; top: 2278px; width: 440px; height: 440px; border-radius: 50%; background: var(--accent-gradient); padding: 9px; }
  .contact-photo div { width: 100%; height: 100%; border-radius: 50%; background: radial-gradient(circle at 45% 40%, #e7c9b5 0%, #b88c78 45%, #3b3b48 100%); }

  /* Footer */
  .footer-nav { position: absolute; top: 2978px; left: 0; width: 1200px; display: flex; justify-content: center; gap: 28px; font-size: 17px; font-weight: 700; text-transform: uppercase; }
  .footer-nav .sep { font-weight: 500; }
  .footer-mail { left: 0; width: 1200px; top: 3015px; text-align: center; font-size: 16px; font-weight: 600; display: flex; justify-content: center; align-items: center; gap: 10px; }
  .footer-rule { left: 111px; top: 3055px; width: 978px; height: 1px; background: rgba(255,255,255,0.18); }
  .copyright { left: 0; width: 1200px; top: 3076px; text-align: center; font-size: 12.5px; font-weight: 500; }
  .social { position: absolute; top: 3066px; width: 36px; height: 36px; border-radius: 50%; background: var(--white); }
  .social.is-active { background: var(--accent-gradient); }
</style>
</head>
<body>

<!-- Background shapes -->
<svg class="abs" style="left:0;top:0" width="1200" height="3111" viewBox="0 0 1200 3111" aria-hidden="true">
  <defs>
    <linearGradient id="heroPhoto" x1="0" y1="0" x2="1" y2="1">
      <stop offset="0" stop-color="#7fa6bd"/>
      <stop offset="0.45" stop-color="#c9b8b8"/>
      <stop offset="1" stop-color="#9fc0d2"/>
    </linearGradient>
    <linearGradient id="techBand" x1="0" y1="0" x2="1" y2="0">
      <stop offset="0" stop-color="#7a2fc4"/>
      <stop offset="0.5" stop-color="#5a68d8"/>
      <stop offset="1" stop-color="#19c9e0"/>
    </linearGradient>
    <linearGradient id="accent" x1="0" y1="0" x2="1" y2="0">
      <stop offset="0" stop-color="#8e2bd0"/>
      <stop offset="1" stop-color="#18d2e6"/>
    </linearGradient>
  </defs>

  <!-- hero arc -->
  <path d="M0,0 H1200 V210 Q1030,690 600,664 Q260,646 0,488 Z" fill="#8e2bd0"/>
  <path d="M0,0 H1200 V180 Q1020,650 600,636 Q260,624 0,476 Z" fill="url(#heroPhoto)" role="img" aria-label="Photo of a hand holding a glowing heart in a lab"/>
  <path d="M0,0 H1200 V180 Q1020,650 600,636 Q260,624 0,476 Z" fill="#06053f" opacity="0.18"/>

  <!-- hero badge -->
  <circle cx="600" cy="640" r="57" fill="#06053f" stroke="#ffffff" stroke-width="2"/>
  <circle cx="600" cy="640" r="37" fill="#ffffff"/>
  <circle cx="600" cy="640" r="22" fill="url(#accent)"/>

  <!-- technologies band -->
  <path d="M0,1735 Q300,1420 600,1420 Q960,1420 1200,1650 V2161 H0 Z" fill="#8e2bd0"/>
  <path d="M0,1748 Q300,1432 600,1432 Q960,1432 1200,1668 V2161 H0 Z" fill="url(#techBand)"/>

  <!-- footer -->
  <path d="M0,3111 V3000 Q300,2792 600,2792 Q900,2792 1200,3020 V3111 Z" fill="#8e2bd0"/>
  <path d="M0,3111 V3040 Q320,2806 620,2806 Q900,2808 1200,3050 V3111 Z" fill="#060537"/>
</svg>

<!-- Header -->
<header>
  <div class="brand" style="left:111px;top:24px;">
    <span class="brand-dot"></span>
    <span class="brand-name">NEVRA</span>
  </div>
  <nav class="main-nav">
    <a class="is-active">Home</a>
    <a>About Us</a>
    <a>Technology</a>
    <a>Publications</a>
  </nav>
  <div class="nav-cta">CONTACT US</div>
</header>

<!-- Hero -->
<section class="hero">
  <h1 class="abs hero-title">Revolutionizing Biomedical Science for a Healthier Tomorrow</h1>
  <p class="abs hero-lead">Innovative tech and research driving human health forward.</p>
  <div class="btn" style="left:111px;top:428px;width:150px;height:47px;">Learn More</div>
</section>

<!-- About -->
<section class="about">
  <div class="abs about-frame"></div>
  <div class="abs about-photo" role="img" aria-label="Photo of a doctor measuring a patient's blood pressure"></div>
  <h2 class="abs section-title about-title">The Future of Biomedicine Begins Here</h2>
  <div class="abs about-copy">
    <p>Sed ut perspiciatis unde omnis iste natus error sit voluptatem accusantium doloremque laudantium, totam rem aperiam, eaque ipsa quae ab illo inventore veritatis et quasi architecto beatae vitae dicta sunt explicabo. Nemo enim ipsam voluptatem quia voluptas sit aspernatur aut odit aut fugit, sed quia consequuntur magni dolores eos qui rationea.</p>
    <p>Sed ut perspiciatis unde omnis iste natus error sit voluptatem accusantium doloremque laudantium, totam rem aperiam, eaque ipsa quae ab illo inventore veritatis et quasi architecto beatae vitae dicta sunt explicabo.</p>
  </div>
  <div class="btn" style="left:599px;top:1258px;width:151px;height:47px;">Learn More</div>
</section>

<!-- Technologies -->
<section class="technologies">
  <h2 class="abs section-title tech-heading">Our Technologies</h2>
  <p class="abs tech-intro">Sed ut perspiciatis unde omnis iste natus error sit voluptatem accusantium doloremque laudantium, totam rem aperiam, eaque ipsa quae ab illo inventore veritatis et quasi architecto beatae vitae dicta sunt explicabo. Nemo enim ipsam voluptatem quia voluptas sit aspernaturea.</p>

  <article class="tech-card" style="left:111px;">
    <div class="tech-icon soft">
      <svg width="52" height="52" viewBox="0 0 52 52" aria-hidden="true">
        <path d="M26 24 C18 17 14 10 20 7 C23 6 25 8 26 10 C27 8 29 6 32 7 C38 10 34 17 26 24 Z" fill="#7b3fe4"/>
        <path d="M8 26 V40 L20 46 H30 M44 26 V40 L32 46" stroke="#7b3fe4" stroke-width="4" fill="none" stroke-linecap="round"/>
      </svg>
    </div>
    <h3>Lorem Ipsum Dol</h3>
    <p>Sed ut perspiciatis unde omnis iste natus error sit voluptatem acc usantium dolorea riam, eaque ipsa quae ab illo inventore veritatis et quasi architecto beatae vitae dicta explicaboea.</p>
  </article>

  <article class="tech-card" style="left:448px;">
    <div class="tech-icon solid">
      <svg width="52" height="52" viewBox="0 0 52 52" aria-hidden="true">
        <path d="M32 42 C22 34 18 28 22 24 C25 21 29 23 32 27 C35 23 39 21 42 24 C46 28 42 34 32 42 Z" fill="#ffffff"/>
        <path d="M14 8 V22 M14 22 A5 5 0 1 0 14.01 22" stroke="#ffffff" stroke-width="3" fill="none"/>
      </svg>
    </div>
    <h3>Lorem Ipsum Dol</h3>
    <p>Sed ut perspiciatis unde omnis iste natus error sit voluptatem acc usantium dolorea riam, eaque ipsa quae ab illo inventore veritatis et quasi architecto beatae vitae dicta explicaboea.</p>
  </article>

  <article class="tech-card" style="left:786px;">
    <div class="tech-icon soft">
      <svg width="56" height="56" viewBox="0 0 56 56" aria-hidden="true">
        <g stroke="#7b3fe4" stroke-width="3">
          <line x1="12" y1="14" x2="28" y2="26"/><line x1="28" y1="26" x2="44" y2="12"/>
          <line x1="28" y1="26" x2="16" y2="42"/><line x1="28" y1="26" x2="42" y2="40"/>
        </g>
        <circle cx="12" cy="14" r="5" fill="#7b3fe4"/><circle cx="44" cy="12" r="5" fill="#3a6fe0"/>
        <circle cx="28" cy="26" r="6" fill="#7b3fe4"/><circle cx="16" cy="42" r="5" fill="#3a6fe0"/>
        <circle cx="42" cy="40" r="5" fill="#7b3fe4"/>
      </svg>
    </div>
    <h3>Lorem Ipsum Dol</h3>
    <p>Sed ut perspiciatis unde omnis iste natus error sit voluptatem acc usantium dolorea riam, eaque ipsa quae ab illo inventore veritatis et quasi architecto beatae vitae dicta explicaboea.</p>
  </article>
</section>

<!-- Contact -->
<section class="contact">
  <h2 class="abs section-title contact-title">Contact Us</h2>
  <span class="field-label" style="left:110px;top:2363px;">First Name</span>
  <span class="field-label" style="left:343px;top:2363px;">Last Name</span>
  <div class="field" style="left:111px;top:2394px;width:224px;height:45px;"></div>
  <div class="field" style="left:343px;top:2394px;width:224px;height:45px;"></div>
  <span class="field-label" style="left:110px;top:2449px;">Phone</span>
  <span class="field-label" style="left:343px;top:2449px;">Email</span>
  <div class="field" style="left:111px;top:2480px;width:224px;height:45px;"></div>
  <div class="field" style="left:343px;top:2480px;width:224px;height:45px;"></div>
  <span class="field-label" style="left:110px;top:2535px;">Enquiry</span>
  <div class="field" style="left:111px;top:2566px;width:456px;height:70px;"></div>
  <div class="btn" style="left:394px;top:2650px;width:172px;height:47px;">Send Message</div>
  <div class="abs contact-photo">
    <div role="img" aria-label="Photo of a patient wearing a forehead light sensor connected to a handheld monitor"></div>
  </div>
</section>

<!-- Footer -->
<footer>
  <div class="brand" style="left:469px;top:2881px;">
    <span class="brand-dot" style="width:70px;height:70px;"></span>
    <span class="brand-name">NEVRA</span>
  </div>
  <nav class="footer-nav">
    <span>Home</span><span class="sep">/</span>
    <span>About Us</span><span class="sep">/</span>
    <span>Technology</span><span class="sep">/</span>
    <span>Publications</span><span class="sep">/</span>
    <span>Contact Us</span>
  </nav>
  <div class="abs footer-mail">
    <svg width="16" height="12" viewBox="0 0 16 12" aria-hidden="true"><rect x="1" y="1" width="14" height="10" rx="1" fill="none" stroke="#18d2e6" stroke-width="1.5"/><path d="M1 2 L8 7 L15 2" fill="none" stroke="#18d2e6" stroke-width="1.5"/></svg>
    <span>info@nevra.com</span>
  </div>
  <div class="abs footer-rule"></div>
  <div class="abs copyright">2025 © ALL RIGHTS RESERVED.</div>
  <span class="social is-active" style="left:967px;" aria-label="Social link"></span>
  <span class="social" style="left:1009px;" aria-label="Social link"></span>
  <span class="social" style="left:1052px;" aria-label="Social link"></span>
</footer>

</body>
</html>
```